New Brand - Website Design (4 Pages)

We are launching a new brand for electronic cigarettes. We already have logo and packaging done and would like a web design to go with it.

We are interested in the following deliverables:

1) Home Page Design
2) Check Out Design
3) How it Works Page
4) Secondary Template Page Design

Looking for a 60s modern look and something that is consistent with our logo and packaging.

Industry/Entity Type

Electronic

Requirements
Must have
• Consistent with logo and packaging (Use Logo Attached)
White background

Example (Functionality & Design): http://www.moltrafen.co.uk/
Example (Design): http://www.brendolark.com/

We want the design more like brendolark but the functionality the same as moltrafen.

Top Bar: Pale Dunes Kits; Cartridge Refills; How it Works; Contact; My Account; Checkout
Should not have
• Stock List or Search Bar or Newsletter Signup

```html
<!DOCTYPE html>
<html lang="en">
<head>
<meta charset="utf-8">
<title>Pale Dunes – Home</title>
<link href="https://fonts.googleapis.com/css2?family=Arimo:wght@400;700&display=swap" rel="stylesheet">
<style>
:root{
  --sky:#a6d5f3;
  --ink:#000;
  --night:#1c1f24;
  --paper:#ebebeb;
  --paper-dark:#d9d9d9;
  --link:#1a8fd0;
  --teal:#3aa7b2;
  --text:#4a4a4a;
  --muted:#5e6670;
  --white:#fff;
}
*{box-sizing:border-box;margin:0;padding:0}
html,body{width:1162px;height:1200px;overflow:hidden}
body{position:relative;font-family:"Arimo",Arial,sans-serif;background:var(--paper);color:var(--text)}
.abs{position:absolute}
h1,h2,h3{font-weight:400}

.top-strip{left:0;top:0;width:1162px;height:11px;background:var(--sky)}
.site-header{left:0;top:11px;width:1162px;height:94px;background:var(--ink)}
.brand{left:190px;top:29px;display:flex;align-items:center;gap:9px}
.brand-dot{width:54px;height:54px;border-radius:50%;background:var(--sky)}
.brand-name{color:var(--white);font-size:25px;font-weight:700;letter-spacing:.5px}
.main-nav{left:526px;top:51px;display:flex;gap:5px;font-size:11.2px;color:var(--white);white-space:nowrap}
.main-nav .sep{color:#ccc}
.main-nav .active{color:var(--sky);position:relative;padding:0 2px 4px;border-bottom:2px solid var(--sky)}
.main-nav .active::after{content:"";position:absolute;left:50%;bottom:-7px;margin-left:-4px;border:4px solid transparent;border-top-color:var(--sky);border-bottom:0}

.hero{left:0;top:105px;width:1162px;height:348px;background:var(--sky)}
.hero-title{left:193px;top:184px;font-size:38px;line-height:44px;color:var(--white)}
.hero-copy{left:194px;top:231px;font-size:18.4px;line-height:22.4px;color:var(--muted);white-space:nowrap}
.btn-buy{left:194px;top:329px;width:139px;height:38px;border-radius:3px;background:linear-gradient(100deg,#2d2f33 0 27%,#4b4e54 27% 100%);color:var(--sky);font-size:18px;line-height:38px;padding-left:31px;box-shadow:0 1px 2px rgba(0,0,0,.3)}
.hero-visual{left:542px;top:141px;width:380px;height:290px;border-radius:4px;background:radial-gradient(ellipse at 72% 68%,#f4f4f4 0 22%,transparent 40%),linear-gradient(125deg,#2b2b2b 0%,#2b2b2b 45%,#b9533f 62%,var(--sky) 100%)}
.arrow{top:245px}
.slide-dots{left:571px;top:431px;display:flex;gap:6px}
.slide-dots span{width:13px;height:13px;border-radius:50%;background:var(--white)}
.slide-dots span.on{background:#1566b8}

.intro-title{left:0;top:475px;width:1162px;text-align:center;font-size:29px;color:#1b1b1b}
.intro-rule{top:514px;height:1px;background:#9a9a9a;width:170px}
.intro-dots{left:519px;top:511px;display:flex;gap:6px}
.intro-dots span{width:11px;height:11px;border-radius:50%;border:2.5px solid var(--teal)}
.intro-copy{left:196px;top:531px;width:770px;text-align:center;font-size:9.6px;line-height:14px}

.feature-band{left:0;top:570px;width:1162px;height:286px;background:var(--paper-dark)}
.card{width:246px}
.card-frame{width:246px;height:133px;background:#f3f3f3;padding:4px;box-shadow:0 0 2px rgba(0,0,0,.25)}
.card-photo{width:100%;height:100%}
.card-title{margin-top:13px;margin-left:-2px;font-size:19px;color:var(--link)}
.card-copy{margin-top:12px;font-size:9.6px;line-height:11.2px;padding-left:2px;white-space:nowrap}
.card-more{display:block;margin-top:11px;font-size:9.6px;font-weight:700;color:var(--link);padding-left:2px}

.tile{top:883px;width:246px;height:153px;background:#f3f3f3;padding:4px;box-shadow:0 0 2px rgba(0,0,0,.25)}
.tile-photo{position:relative;width:100%;height:100%}
.tile-label{position:absolute;color:var(--white);font-size:18px;line-height:20px;white-space:nowrap;text-shadow:0 0 2px #000,0 0 3px #000}

.accent-strip{left:0;top:1072px;width:1162px;height:10px;background:var(--sky)}
.site-footer{left:0;top:1082px;width:1162px;height:118px;background:var(--night)}
.footer-nav{left:194px;top:1109px;font-size:9.6px;color:var(--white);display:flex;gap:5px}
.copyright{left:193px;top:1135px;font-size:9.6px;color:var(--white)}
.social{left:869px;top:1102px;display:flex;gap:5px}
.social span{width:29px;height:29px;border-radius:50%;background:#cfcfcf;box-shadow:0 0 0 2px #4a4a4a}
.payments{left:803px;top:1138px;display:flex;gap:3px}
.payments span{width:39px;height:22px;background:#efefef;border-radius:2px}
.edition{left:1017px;top:1126px;font-size:10px;color:var(--white)}
</style>
</head>
<body>
<div class="abs top-strip"></div>
<header class="abs site-header"></header>
<div class="abs brand"><span class="brand-dot"></span><span class="brand-name">Pale Dunes</span></div>
<nav class="abs main-nav">
  <span class="active">Pale Dunes Kits</span><span class="sep">\</span>
  <span>Cartridge Refills</span><span class="sep">\</span>
  <span>How it Works</span><span class="sep">\</span>
  <span>Contact</span><span class="sep">\</span>
  <span>My Account</span><span class="sep">\</span>
  <span>Checkout</span>
</nav>

<section class="abs hero"></section>
<svg class="abs arrow" style="left:72px" width="16" height="28" viewBox="0 0 16 28"><path d="M13 2 3 14l10 12" fill="none" stroke="#666" stroke-width="2.5"/></svg>
<svg class="abs arrow" style="left:1078px" width="16" height="28" viewBox="0 0 16 28"><path d="M3 2l10 12L3 26" fill="none" stroke="#666" stroke-width="2.5"/></svg>
<h1 class="abs hero-title">Pale Dune</h1>
<p class="abs hero-copy">Lorem ipsum dolor sit amet,<br>consectetur adipiscing elit.<br>Nulla convallis egestas rhon-<br>cus. Donec facilisis fermentum</p>
<div class="abs btn-buy">Buy Now</div>
<div class="abs hero-visual" role="img" aria-label="Product packaging: two cartomiser boxes, black with white and orange sides"></div>
<div class="abs slide-dots"><span class="on"></span><span></span><span></span></div>

<h2 class="abs intro-title">Pale Dunes</h2>
<div class="abs intro-rule" style="left:338px"></div>
<div class="abs intro-rule" style="left:600px"></div>
<div class="abs intro-dots"><span></span><span></span><span></span></div>
<p class="abs intro-copy">Lorem ipsum dolor sit amet, consectetur adipiscing elit. Nulla convallis egestas rhoncus. Donec facilisis fermentum sem, ac viverra ante luctus vel. Donec vel mauris quam. Aliquam<br>pellentesque pellentesque turpis, ut bibendum sapien sollicitudin nec.</p>

<section class="abs feature-band"></section>
<article class="abs card" style="left:194px;top:587px">
  <div class="card-frame"><div class="card-photo" role="img" aria-label="Photo of a man using an electronic cigarette" style="background:radial-gradient(ellipse at 75% 40%,#a07a5c 0,#5a4535 40%,#2a221d 80%)"></div></div>
  <h3 class="card-title">E-Cigarettes</h3>
  <p class="card-copy">Lorem ipsum dolor sit amet, consectetur adipiscing elit.<br>Nulla convallis egestas rhoncus. Donec facilisis fermen-<br>tum sem, ac viverra ante luctus vel. Donec vel mauris<br>quam. Aliquam pellentesque pellentesque turpis, ut<br>bibendum sapien sollicitudin nec.</p>
  <span class="card-more">Read More..</span>
</article>
<article class="abs card" style="left:458px;top:587px">
  <div class="card-frame"><div class="card-photo" role="img" aria-label="Street map showing shop locations" style="background:radial-gradient(circle at 75% 50%,#efece4 0,#e4e0d6 45%,#d7d3c8 100%)"></div></div>
  <h3 class="card-title">Find Shop</h3>
  <p class="card-copy">Lorem ipsum dolor sit amet, consectetur adipiscing elit.<br>Nulla convallis egestas rhoncus. Donec facilisis fermen-<br>tum sem, ac viverra ante luctus vel. Donec vel mauris<br>quam. Aliquam pellentesque pellentesque turpis, ut<br>bibendum sapien sollicitudin nec.</p>
  <span class="card-more">Read More..</span>
</article>
<article class="abs card" style="left:723px;top:587px">
  <div class="card-frame"><div class="card-photo" role="img" aria-label="Row of coloured flavour cartridges" style="background:linear-gradient(180deg,#2c2c2c 0 30%,transparent 30%),linear-gradient(90deg,#9bb048,#c9b53a,#5a78b8,#a55ab8,#c8c8c8,#6aaa4a)"></div></div>
  <h3 class="card-title">Flavours</h3>
  <p class="card-copy">Lorem ipsum dolor sit amet, consectetur adipiscing elit.<br>Nulla convallis egestas rhoncus. Donec facilisis fermen-<br>tum sem, ac viverra ante luctus vel. Donec vel mauris<br>quam. Aliquam pellentesque pellentesque turpis, ut<br>bibendum sapien sollicitudin nec.</p>
  <span class="card-more">Read More..</span>
</article>

<div class="abs tile" style="left:194px">
  <div class="tile-photo" role="img" aria-label="Laboratory with workers preparing liquids" style="background:linear-gradient(135deg,#5f7d96,#b8c4cc 55%,#7e878d)">
    <svg class="abs" style="left:120px;top:30px" width="32" height="32" viewBox="0 0 32 32"><circle cx="16" cy="16" r="15" fill="#1a6fc2" stroke="#cfe8f8" stroke-width="2"/><path d="M13 9l7 7-7 7" fill="none" stroke="#fff" stroke-width="3"/></svg>
    <span class="tile-label" style="left:64px;top:112px">How It Works</span>
  </div>
</div>
<div class="abs tile" style="left:456px">
  <div class="tile-photo" role="img" aria-label="Promotional banner for a new vaporiser" style="background:radial-gradient(ellipse at 70% 60%,#6f8ea8 0,#4f6880 45%,#3c5468 100%)">
    <span class="tile-label" style="left:78px;top:68px">Order Now</span>
  </div>
</div>
<div class="abs tile" style="left:721px;padding:0">
  <div class="tile-photo" role="img" aria-label="Vintage tobacco advertisement" style="background:linear-gradient(90deg,#cfc9ba,#a9aaa2 45%,#6f8292)">
    <span class="tile-label" style="left:107px;top:68px">Ads</span>
  </div>
</div>

<div class="abs accent-strip"></div>
<footer class="abs site-footer"></footer>
<nav class="abs footer-nav"><span>Home</span><span>|</span><span>About us</span><span>|</span><span>Counselling</span><span>|</span><span>Workshop</span><span>|</span><span>Contact us</span></nav>
<p class="abs copyright">Content copyright 2013. BRIGHTMERIDIAN.CA. All rights reserved.</p>
<div class="abs social" aria-label="Social links"><span></span><span></span><span></span></div>
<div class="abs payments" aria-label="Accepted payment methods"><span></span><span></span><span></span><span></span></div>
<span class="abs edition">X18</span>
</body>
</html>
```